RTavenor Business Cards & Letterhead

I have a logo but need a design for some new business cards. We are a Design-Build Firm that specializes in the design and construction of commercial projects.
the cards need to be professional. no cartoon stuff.
i would like to have the cards in AI format so I can update the card as needed. Logo is provided.
Our Address is: 4187 Marlowe Ct. Fenwick, North Alder 27614

```html
<!DOCTYPE html>
<html lang="en">
<head>
<meta charset="utf-8">
<title>RTavenor Business Card</title>
<link href="https://fonts.googleapis.com/css2?family=Montserrat:wght@400;500;800&display=swap" rel="stylesheet">
<style>
  :root {
    --bg-light: #ececec;
    --bg-dark: #b9b9b9;
    --card-white: #fdfdfd;
    --card-grey: #ececec;
    --ink-grey: #5e5f63;
    --soft-grey: #6f7074;
    --band-grey: #5a5b5f;
    --brand-blue: #1c5a8a;
    --brand-blue-light: #4a8bb5;
    --accent-blue: #3a7db0;
    --paper: #ffffff;
  }
  * { box-sizing: border-box; margin: 0; padding: 0; }
  html, body { width: 1200px; height: 1200px; overflow: hidden; }
  body {
    background: linear-gradient(135deg, var(--bg-light), var(--bg-dark));
    font-family: "Montserrat", sans-serif;
    position: relative;
  }
  .card {
    position: absolute;
    left: 220px;
    width: 760px;
    height: 434px;
    border-radius: 28px;
    overflow: hidden;
    box-shadow: 0 10px 30px rgba(0,0,0,0.18);
  }
  .card--front { top: 100px; background: var(--card-white); }
  .card--back { top: 640px; background: linear-gradient(160deg, var(--paper), var(--card-grey)); }

  .brand { display: flex; align-items: center; gap: 12px; }
  .brand__mark { width: 34px; height: 34px; background: var(--brand-blue); }
  .brand__name {
    font-weight: 800;
    color: var(--ink-grey);
    letter-spacing: 1px;
  }
  .card--front .brand {
    position: absolute; left: 50%; top: 50%;
    transform: translate(-50%, -50%);
  }
  .card--front .brand__name { font-size: 64px; }
  .card--front .brand__mark { width: 50px; height: 50px; }

  .card--back .brand { position: absolute; right: 60px; top: 60px; }
  .card--back .brand__name { font-size: 38px; }
  .card--back .brand__mark { width: 28px; height: 28px; }

  .holder { position: absolute; left: 60px; top: 120px; }
  .holder__name { font-size: 30px; font-weight: 800; color: var(--accent-blue); }
  .holder__title { font-size: 17px; font-weight: 500; color: var(--soft-grey); margin-top: 4px; margin-left: 12px; }

  .contacts { position: absolute; left: 80px; top: 228px; list-style: none; }
  .contacts li {
    display: flex; align-items: center; gap: 10px;
    font-size: 18px; color: var(--ink-grey); line-height: 30px;
  }
  .contacts svg { width: 16px; height: 16px; fill: var(--brand-blue); }

  .waves { position: absolute; inset: 0; width: 100%; height: 100%; }
  .address {
    position: absolute; right: 90px; bottom: 26px;
    color: var(--paper); font-size: 19px; font-weight: 500; letter-spacing: 0.5px;
    white-space: nowrap;
  }
</style>
</head>
<body>
  <section class="card card--front" aria-label="Card front">
    <div class="brand">
      <span class="brand__mark"></span>
      <span class="brand__name">RTAVENOR</span>
    </div>
  </section>

  <section class="card card--back" aria-label="Card back">
    <svg class="waves" viewBox="0 0 760 434" preserveAspectRatio="none">
      <defs>
        <linearGradient id="blueBand" x1="0" y1="0" x2="1" y2="0">
          <stop offset="0" stop-color="var(--brand-blue-light)"/>
          <stop offset="0.5" stop-color="var(--brand-blue)"/>
          <stop offset="1" stop-color="var(--brand-blue)"/>
        </linearGradient>
      </defs>
      <path d="M0 320 Q 430 372 760 180 L760 434 L0 434 Z" fill="var(--band-grey)"/>
      <path d="M0 340 Q 430 392 760 204 L760 434 L0 434 Z" fill="url(#blueBand)"/>
    </svg>

    <div class="brand">
      <span class="brand__mark"></span>
      <span class="brand__name">RTAVENOR</span>
    </div>

    <div class="holder">
      <p class="holder__name">Renata Tavenor</p>
      <p class="holder__title">President</p>
    </div>

    <ul class="contacts">
      <li>
        <svg viewBox="0 0 24 24"><path d="M6.6 10.8a15.5 15.5 0 0 0 6.6 6.6l2.2-2.2c.3-.3.7-.4 1-.2 1.1.4 2.3.6 3.6.6.6 0 1 .4 1 1V20c0 .6-.4 1-1 1C10.6 21 3 13.4 3 4c0-.6.4-1 1-1h3.5c.6 0 1 .4 1 1 0 1.3.2 2.5.6 3.6.1.3 0 .7-.2 1z"/></svg>
        (919)-555-0142
      </li>
      <li>
        <svg viewBox="0 0 24 24"><path d="M2 5h20v14H2z M2 5l10 8 10-8" /></svg>
        info@rtavenor.com
      </li>
      <li>
        <svg viewBox="0 0 24 24"><path d="M12 2a10 10 0 1 0 0 20 10 10 0 0 0 0-20zm-1 17.9A8 8 0 0 1 4.1 13H8c.1 2.5.9 5 3 6.9zM8 11H4.1A8 8 0 0 1 11 4.1C8.9 6 8.1 8.5 8 11zm2 0c.1-2.4 1-4.6 2-6 1 1.4 1.9 3.6 2 6zm0 2h4c-.1 2.4-1 4.6-2 6-1-1.4-1.9-3.6-2-6zm3 6.9c2.1-1.9 2.9-4.4 3-6.9h3.9a8 8 0 0 1-6.9 6.9zM16 11c-.1-2.5-.9-5-3-6.9a8 8 0 0 1 6.9 6.9z"/></svg>
        www.rtavenor.com
      </li>
    </ul>

    <p class="address">4187 Marlowe Ct. Fenwick, North Alder 27614</p>
  </section>
</body>
</html>
```